Corvane Property Care Email Marketing Design

Dear Designer,
We're in need of an email background template for our company, Corvane Property Care, that reflects our commitment to building lasting relationships with our clients and providing top-quality restoration and cleaning services.
We'd like the template to incorporate our brand colors, which are #F2F2F3, #005EA5, #468ECC, and #000000, and to feature images related to our services, such as water restoration, emergency flood response, mold remediation, trauma scene clean-up, fire restoration, carpet cleaning, and more. Our logo and tagline, "Disaster Undone", should be prominently displayed in a unique and visually appealing way, along with our website address, www.corvanepropertycare-demo.net.
The email should be professional and positive, highlighting the camaraderie and teamwork among our employees. We want to thank our clients for their business, offer a special discount, and promote our services. The final design should be visually stunning and memorable, with a clear call-to-action to encourage clients to take advantage of the discount.
We'd like the final design in JPG or PNG format, with a resolution of at least 720x720 pixels.
Thank you for considering this project. We're excited to see what you come up with!
Best regards,
Tomas

```html
<!DOCTYPE html>
<html lang="en">
<head>
<meta charset="utf-8">
<title>Corvane Property Care – Disaster Undone</title>
<link rel="stylesheet" href="https://fonts.googleapis.com/css2?family=Cinzel:wght@400;600&family=Marcellus&family=Cabin:wght@400&display=swap">
<style>
  :root {
    --brand-blue: #1f4a7e;
    --ring-blue: #2c5f9c;
    --ink: #000000;
    --paper: #f2f2f3;
    --white: #ffffff;
    --dark-1: #0d0f12;
    --dark-2: #23262b;
  }
  * { margin: 0; padding: 0; box-sizing: border-box; }
  html, body { width: 1200px; height: 1200px; overflow: hidden; background: var(--ink); }
  .canvas { position: relative; width: 1200px; height: 1200px; overflow: hidden; color: var(--white); }

  .masthead {
    position: absolute; left: 0; top: 0; width: 1200px; height: 158px;
    background: radial-gradient(ellipse at 50% 40%, #2a2d31 0%, #101114 70%, #050506 100%);
  }
  .brand-name {
    position: absolute; left: 0; top: 48px; width: 1200px; text-align: center;
    font-family: "Cinzel", serif; font-weight: 600; font-size: 40px; letter-spacing: 2px;
    color: var(--white);
  }

  .tagline-band {
    position: absolute; left: 0; top: 158px; width: 1200px; height: 150px;
    background: var(--brand-blue);
    display: flex; align-items: center; justify-content: center;
  }
  .tagline {
    font-family: "Cinzel", serif; font-weight: 400; font-size: 68px; letter-spacing: 2px;
    color: var(--white);
  }

  .services {
    position: absolute; left: 0; top: 308px; width: 1200px; height: 797px;
    background: linear-gradient(160deg, var(--dark-2) 0%, var(--dark-1) 55%, #16181c 100%);
  }
  .services-title {
    position: absolute; left: 0; top: 50px; width: 1200px; text-align: center;
    font-family: "Marcellus", serif; font-size: 66px; color: var(--white);
  }
  .service {
    position: absolute; display: flex; align-items: center;
  }
  .service-photo {
    width: 138px; height: 138px; border-radius: 50%;
    border: 5px solid var(--ring-blue);
    flex: none;
  }
  .service-label {
    margin-left: 35px;
    font-family: "Marcellus", serif; font-size: 32px; line-height: 50px;
    text-transform: uppercase; color: var(--white);
  }
  .service--water  { left: 101px; top: 181px; }
  .service--mold   { left: 684px; top: 181px; }
  .service--fire   { left: 101px; top: 381px; }
  .service--trauma { left: 684px; top: 381px; }
  .photo-water  { background: radial-gradient(circle at 40% 40%, #c9ccd0, #7d838a 80%); }
  .photo-mold   { background: radial-gradient(circle at 50% 40%, #e8eaee, #3a3f47 80%); }
  .photo-fire   { background: radial-gradient(circle at 50% 50%, #6b5a4a, #22201e 85%); }
  .photo-trauma { background: radial-gradient(circle at 50% 50%, #8a4a2a, #1a1414 85%); }

  .services-copy {
    position: absolute; left: 105px; top: 575px; width: 990px; text-align: center;
    font-family: "Cabin", sans-serif; font-size: 26px; line-height: 50px; color: var(--white);
  }

  .footer-band {
    position: absolute; left: 0; top: 1105px; width: 1200px; height: 95px;
    background: var(--brand-blue);
  }
  .website {
    position: absolute; left: 0; top: 0; width: 1200px; line-height: 95px; text-align: center;
    font-family: "Cabin", sans-serif; font-size: 28px; color: var(--white);
  }
  .ref-code {
    position: absolute; right: 42px; top: 0; line-height: 95px;
    font-family: "Cabin", sans-serif; font-size: 17px; color: var(--white);
  }
</style>
</head>
<body>
<div class="canvas">
  <header class="masthead" role="img" aria-label="Dark background covered in water droplets">
    <div class="brand-name">CORVANE PROPERTY CARE</div>
  </header>

  <div class="tagline-band">
    <h1 class="tagline">DISASTER UNDONE</h1>
  </div>

  <section class="services" role="img" aria-label="Dimly lit modern interior with large windows">
    <h2 class="services-title">Our Service</h2>

    <div class="service service--water">
      <div class="service-photo photo-water" role="img" aria-label="Water droplets on a surface"></div>
      <div class="service-label">Water<br>Restoration</div>
    </div>
    <div class="service service--mold">
      <div class="service-photo photo-mold" role="img" aria-label="Worker in protective suit for mold remediation"></div>
      <div class="service-label">Mold<br>Remediation</div>
    </div>
    <div class="service service--fire">
      <div class="service-photo photo-fire" role="img" aria-label="Fire damaged building interior"></div>
      <div class="service-label">Fire and Smoke<br>Restoration</div>
    </div>
    <div class="service service--trauma">
      <div class="service-photo photo-trauma" role="img" aria-label="Scene cordoned off with tape at night"></div>
      <div class="service-label">Trauma<br>Clean Up</div>
    </div>

    <p class="services-copy">Our friendly team of experienced professionals are ready to get started on your cleaning project. Corvane Property Care knows how to deliver the results you deserve – every time. Give us a call and we can be to you within an hour anywhere in Las Vegas.</p>
  </section>

  <footer class="footer-band">
    <div class="website">www.corvanepropertycare-demo.net.</div>
    <div class="ref-code">C38</div>
  </footer>
</div>
</body>
</html>
```